Dermatology at Your Door Logo and business card

We provide dermatological services to the community. This includes Assisted Living Facilities, nursing homes and to large cooperation, Health fairs etc. We provide a health care provider that travels to institutions, providing these services. All procedures and surgeries are done onsite in one of our state of the art mobile clinics. We provide services including, but not limited to; skin biopsies, skin surgeries , surgical procedures including skin cancer removal mole removal and treatment of various skin disorders. we bring mobile Dermatology to you.

Industry/Entity Type

Business

Contact Information for Business Card

Need Logo address phone number, email website

Logo Text

Dermatology at Your Door

Logo styles of interest
Emblem Logo
Abstract Logo
Character Logo
Lettermark Logo
Requirements
Must have
• Marcus Tilden ARNP DN-C
• Medical Facilitator
• P. (407) 555-3914
• Fax (386) 555-7281

```html
<!DOCTYPE html>
<html lang="en">
<head>
<meta charset="UTF-8">
<title>Dermatology at Your Door – Business Card</title>
<link href="https://fonts.googleapis.com/css2?family=Josefin+Sans:wght@300&family=Arimo:wght@400&display=swap" rel="stylesheet">
<style>
  :root {
    --page: #ffffff;
    --card: #135e5b;
    --card-deep: #0f5451;
    --glow: rgba(120, 190, 180, 0.14);
    --text-light: #ffffff;
    --corner-disc: #3f625f;
  }
  * { margin: 0; padding: 0; box-sizing: border-box; }
  html, body {
    width: 1200px;
    height: 703px;
    overflow: hidden;
    background: var(--page);
  }
  .card {
    position: absolute;
    left: 19px;
    top: 19px;
    width: 1162px;
    height: 665px;
    overflow: hidden;
    background:
      radial-gradient(ellipse 70% 45% at 50% 92%, var(--glow), transparent 70%),
      radial-gradient(ellipse 30% 30% at 8% 60%, var(--glow), transparent 70%),
      linear-gradient(180deg, var(--card) 0%, var(--card) 55%, var(--card-deep) 100%);
    color: var(--text-light);
  }
  .corner-disc {
    position: absolute;
    left: 1025px;
    top: 528px;
    width: 168px;
    height: 168px;
    border-radius: 50%;
    background: var(--corner-disc);
  }
  .brand-name {
    position: absolute;
    left: 0;
    top: 170px;
    width: 100%;
    text-align: center;
    font-family: "Josefin Sans", sans-serif;
    font-weight: 300;
    font-size: 62px;
    line-height: 1;
    color: var(--text-light);
  }
  .holder {
    position: absolute;
    left: 0;
    top: 362px;
    width: 100%;
    text-align: center;
    font-family: "Arimo", sans-serif;
    font-weight: 400;
    font-size: 45px;
    letter-spacing: 0.5px;
    line-height: 1;
  }
  .holder .credentials { margin-left: 36px; }
  .role {
    position: absolute;
    left: 0;
    top: 432px;
    width: 100%;
    text-align: center;
    font-family: "Arimo", sans-serif;
    font-size: 36px;
    line-height: 1;
  }
  .contact {
    position: absolute;
    list-style: none;
    font-family: "Arimo", sans-serif;
    font-size: 26px;
    letter-spacing: 1.6px;
  }
  .contact li {
    display: flex;
    align-items: center;
    height: 42px;
  }
  .contact svg {
    width: 30px;
    height: 30px;
    margin-right: 20px;
    fill: var(--text-light);
    flex: none;
  }
  .contact-left { left: 100px; top: 478px; }
  .contact-left li:nth-child(3) { margin-top: 2px; }
  .contact-right { left: 600px; top: 474px; }
</style>
</head>
<body>
  <main class="card">
    <div class="corner-disc"></div>

    <p class="brand-name">Dermatology at Your Door</p>

    <h1 class="holder">MARCUS TILDEN<span class="credentials">ARNP DN-C</span></h1>
    <p class="role">Medical Facilitator</p>

    <ul class="contact contact-left">
      <li>
        <svg viewBox="0 0 24 24" aria-hidden="true"><path d="M12 1.5a7.5 7.5 0 0 0-7.5 7.5c0 5.6 7.5 13.5 7.5 13.5s7.5-7.9 7.5-13.5A7.5 7.5 0 0 0 12 1.5zm0 10.4a2.9 2.9 0 1 1 0-5.8 2.9 2.9 0 0 1 0 5.8z"/></svg>
        <span>2847 W. Harbor Ave. ste #5</span>
      </li>
      <li>
        <svg viewBox="0 0 24 24" aria-hidden="true"><path d="M6.6 2.5l3 3.6-1.8 2.4a12 12 0 0 0 7.7 7.7l2.4-1.8 3.6 3-2.2 3.1C12 20.3 3.7 12 3.5 4.7z"/></svg>
        <span>(407) 555-3914</span>
      </li>
      <li>
        <svg viewBox="0 0 24 24" aria-hidden="true"><path d="M6 2h9l3 3v4H6zM2 10h20v9H2zm3 2v2h3v-2zm5 0v2h2v-2zm4 0v2h2v-2zM6 20h12v2H6z"/></svg>
        <span>(386) 555-7281</span>
      </li>
    </ul>

    <ul class="contact contact-right">
      <li>
        <svg viewBox="0 0 24 24" aria-hidden="true"><path d="M1.5 4.5h21v15h-21zm2 2v.4L12 13l8.5-6.1v-.4zm0 2.8v8.2h17V9.3L12 15.4z"/></svg>
        <span>dermatyourdoor@mailbox.com</span>
      </li>
      <li>
        <svg viewBox="0 0 24 24" aria-hidden="true"><path d="M12 1.5a10.5 10.5 0 1 0 0 21 10.5 10.5 0 0 0 0-21zm-1 2.2V7H7.6A8.6 8.6 0 0 1 11 3.7zm2 0A8.6 8.6 0 0 1 16.4 7H13zM6.6 9H11v2H3.6a8.4 8.4 0 0 1 3-2zm6.4 0h4.4a8.4 8.4 0 0 1 3 2H13zM3.6 13H11v2H6.6a8.4 8.4 0 0 1-3-2zm9.4 0h7.4a8.4 8.4 0 0 1-3 2H13zm-5.4 4H11v3.3A8.6 8.6 0 0 1 7.6 17zm5.4 0h3.4a8.6 8.6 0 0 1-3.4 3.3z"/></svg>
        <span>www.dermatyourdoor.com</span>
      </li>
    </ul>
  </main>
</body>
</html>
```